The Vantor Codex Book Cover

"The Vantor Codex" is a book I wrote with the slogan "Unlock Performance, Spark Engagement: Master the Art of Building Winning Cultures in Today's Hybrid World". The book is designed around a methodology that's mine and that I attached. I would love to see the graphic of the methodology integrated in the design in a very subtle way. Use colors from the model but the book cover should be catchy, modern and engaging to the eye.
Overall the book is about three key elements towards success:
- (Self) Directions (purpose)
- Human experience (people and psychological safety)
- Maximize engagement
The methodology is a FLOW so flow is something that could be incorporated as well in the concept.
Low design quality
Managers and Teams

```html
<!DOCTYPE html>
<html lang="en">
<head>
<meta charset="utf-8">
<title>The Vantor Codex — Book Cover</title>
<link rel="stylesheet" href="https://fonts.googleapis.com/css2?family=Bebas+Neue&family=Cinzel:wght@400&display=swap">
<style>
  :root {
    --ink-white: #ffffff;
    --shadow-deep: #0e0d16;
    --navy-night: #12142a;
    --skin-warm: #a8785a;
    --skin-deep: #5a3a2a;
    --skin-light: #d9b49a;
    --sleeve-dark: #2a2620;
    --flow-pink: #e8557a;
    --flow-orange: #f0a24a;
    --flow-teal: #3fb5c4;
    --flow-green: #8cc86a;
  }
  html, body {
    margin: 0;
    padding: 0;
    overflow: hidden;
    background: var(--shadow-deep);
  }
  .cover {
    position: relative;
    width: 933px;
    height: 1200px;
    overflow: hidden;
    color: var(--ink-white);
    font-family: "Bebas Neue", "Oswald", sans-serif;
  }
  .cover-photo {
    position: absolute;
    inset: 0;
    background:
      radial-gradient(ellipse 55% 35% at 45% 40%, var(--skin-light) 0%, rgba(217,180,154,0) 70%),
      radial-gradient(ellipse 60% 40% at 50% 60%, var(--skin-warm) 0%, rgba(168,120,90,0) 75%),
      radial-gradient(ellipse 50% 30% at 30% 75%, var(--skin-deep) 0%, rgba(90,58,42,0) 80%),
      linear-gradient(180deg, var(--sleeve-dark) 0%, #4a3a30 40%, #3a2a24 70%, var(--navy-night) 100%);
  }
  .cover-shade {
    position: absolute;
    inset: 0;
    background: linear-gradient(180deg,
      rgba(14,13,22,0.35) 0%,
      rgba(14,13,22,0) 20%,
      rgba(14,13,22,0) 45%,
      rgba(14,13,22,0.55) 70%,
      rgba(18,20,42,0.95) 100%);
  }
  .author-name {
    position: absolute;
    top: 42px;
    left: 0;
    width: 100%;
    text-align: center;
    font-family: "Cinzel", serif;
    font-size: 40px;
    letter-spacing: 0.28em;
    margin: 0;
  }
  .tagline {
    position: absolute;
    top: 628px;
    left: 0;
    width: 100%;
    text-align: center;
    font-size: 17px;
    letter-spacing: 0.52em;
    margin: 0;
  }
  .title {
    position: absolute;
    top: 662px;
    left: 0;
    width: 100%;
    text-align: center;
    margin: 0;
    font-weight: 400;
    text-shadow: 0 4px 18px rgba(0,0,0,0.35);
  }
  .title-lead {
    display: block;
    font-size: 112px;
    line-height: 96px;
    letter-spacing: 0.24em;
    padding-left: 0.24em;
  }
  .title-main {
    display: block;
    font-size: 176px;
    line-height: 150px;
    letter-spacing: 0.01em;
  }
  .flow-divider {
    position: absolute;
    top: 925px;
    left: 171px;
    width: 591px;
    height: 64px;
  }
  .flow-rule {
    position: absolute;
    top: 31px;
    width: 200px;
    height: 3px;
    background: var(--ink-white);
  }
  .flow-rule--left { left: 0; }
  .flow-rule--right { right: 0; }
  .flow-mark {
    position: absolute;
    left: 223px;
    top: 0;
    width: 146px;
    height: 64px;
    border-radius: 32px;
    background: linear-gradient(90deg, var(--flow-pink), var(--flow-orange) 35%, var(--flow-teal) 65%, var(--flow-green));
    opacity: 0.9;
  }
  .promise {
    position: absolute;
    top: 1016px;
    left: 0;
    width: 100%;
    text-align: center;
    margin: 0;
    font-size: 40px;
    line-height: 47px;
    letter-spacing: 0.01em;
  }
</style>
</head>
<body>
  <main class="cover">
    <div class="cover-photo" role="img" aria-label="Photo of many hands from a diverse team stacked together in the centre"></div>
    <div class="cover-shade"></div>

    <p class="author-name">Author Name</p>

    <p class="tagline">Unlock Performance, Spark Engagement:</p>

    <h1 class="title">
      <span class="title-lead">The Vantor</span>
      <span class="title-main">Codex</span>
    </h1>

    <div class="flow-divider">
      <span class="flow-rule flow-rule--left"></span>
      <div class="flow-mark" role="img" aria-label="Colourful flow methodology graphic"></div>
      <span class="flow-rule flow-rule--right"></span>
    </div>

    <p class="promise">Master the art of building winning cultures<br>in today's hybrid world</p>
  </main>
</body>
</html>
```